Web Design for company in the healthcare industry

We need a web design for a new company in the healthcare industry (telehealth) which allows patients to schedule appointments at their convenience, view and monitor their results, and consult with specialists that fit their requirements. The aim is to help patients take charge of their own health.

We already have a logo (attached) and are working with a developer who will do all the back end programming once the design is ready. Apart from the colours in the logo, we think shades of gray would work well.

Target Market(s)

I imagine the vast majority would be professionals from 30-50 years old.

Industry/Entity Type

Health And Wellness

Number of Pages Required

4 page

Requirements
Must have
• Hand-sketched graphics, particularly on landing page.
Should not have
• We don't want any photographs of people

```html
<!DOCTYPE html>
<html lang="en">
<head>
<meta charset="utf-8">
<title>Medora Healthcare</title>
<link rel="stylesheet" href="https://fonts.googleapis.com/css2?family=Open+Sans:wght@400;600;700&display=swap">
<style>
:root{
  --blue:#2c7cb8;
  --green:#7cbd3a;
  --ink:#333;
  --muted:#8a8a8a;
  --line:#e3e3e3;
  --hero-a:#f3f3f3;
  --hero-b:#d9d9d9;
  --footer:#2b2b2b;
  --white:#fff;
}
*{box-sizing:border-box;margin:0;padding:0}
html,body{width:769px;height:1200px;overflow:hidden;background:var(--white);font-family:"Open Sans",Arial,sans-serif;color:var(--ink)}
.page{position:relative;width:769px;height:1200px}

.site-header{position:absolute;top:0;left:0;width:769px;height:44px;display:flex;align-items:center;justify-content:space-between;padding:0 44px}
.brand{display:flex;align-items:center;gap:7px;font-size:22px;font-weight:600;color:var(--blue)}
.brand-dot{width:12px;height:12px;border-radius:50%;background:var(--green)}
.main-nav{display:flex;gap:26px;font-size:11px;font-weight:600}
.main-nav a{color:var(--ink);text-decoration:none}

.hero{position:absolute;top:44px;left:0;width:769px;height:276px;background:linear-gradient(180deg,var(--hero-a),var(--hero-b))}
.hero-arrows{position:absolute;left:0;top:0}
.step{position:absolute;width:120px}
.step-label{font-size:10px;line-height:1.3;color:var(--ink)}
.step-label b{display:block;color:var(--green);font-size:12px;font-weight:600}
.step-circle{position:absolute;top:40px;left:0;width:118px;height:118px;border-radius:50%;background:var(--white);border:1px solid var(--line);display:flex;align-items:center;justify-content:center}
.step-art{width:60px;height:44px;border-radius:6px;background:linear-gradient(135deg,#e8e8e8,#c9c9c9)}
.tag-available{position:absolute;top:25px;left:660px;background:var(--green);color:var(--white);font-size:9px;font-weight:600;padding:4px 10px;border-radius:2px}
.doodle{position:absolute;top:48px;left:600px;width:130px;height:210px;border-radius:60px 60px 10px 10px;background:linear-gradient(180deg,#fafafa,#d0d0d0)}

.intro{position:absolute;top:352px;left:44px;width:681px;text-align:center}
.intro h1{font-size:22px;font-weight:400;color:var(--blue)}
.intro p{margin-top:12px;font-size:9.5px;line-height:1.6;color:var(--muted)}

.cards{position:absolute;top:440px;left:115px;display:flex;gap:37px}
.card{width:155px;height:230px;background:var(--white);border:1px solid var(--line);box-shadow:0 2px 4px rgba(0,0,0,.06);text-align:center}
.card-media{height:150px}
.card-media.a{background:linear-gradient(135deg,#6ea6d6,#1f4f86)}
.card-media.b{background:linear-gradient(135deg,#c4d8ee,#4d7fb3)}
.card-media.c{background:linear-gradient(135deg,#9fc3e8,#2a5a92)}
.card h3{margin-top:12px;font-size:11px;font-weight:600;color:var(--green)}
.card p{margin:6px 12px 0;font-size:8.5px;line-height:1.5;color:var(--muted)}

.columns{position:absolute;top:752px;left:44px;width:681px;display:flex;gap:38px}
.col{flex:1}
.col h2{font-size:13px;font-weight:600;color:var(--blue);padding-bottom:10px;border-bottom:1px solid var(--line);margin-bottom:12px}
.col p{font-size:8.5px;line-height:1.6;color:var(--muted)}
.specialist-media{height:80px;background:radial-gradient(circle at 50% 50%,#5e8fd0,#0d1f45);margin-bottom:10px}
.read-more{display:inline-block;margin-top:6px;font-size:8.5px;color:var(--ink);text-decoration:underline}
.checks{list-style:none;margin-top:10px}
.checks li{display:flex;align-items:center;gap:7px;font-size:9px;color:var(--ink);margin-bottom:8px}
.testimonial{display:flex;gap:10px;margin-bottom:16px}
.avatar{flex:none;width:34px;height:34px;border-radius:50%;background:linear-gradient(135deg,#e1c7b0,#9b7a63)}
.testimonial b{display:block;font-size:8.5px;font-weight:600;color:var(--green);margin-bottom:2px}

.site-footer{position:absolute;top:1025px;left:0;width:769px;height:175px;background:var(--footer);text-align:center;color:var(--white)}
.footer-nav{margin-top:38px;display:flex;justify-content:center;gap:18px;font-size:8.5px;font-weight:600}
.footer-nav a{color:var(--white);text-decoration:none}
.copyright{margin-top:14px;font-size:8.5px;color:#bdbdbd;display:flex;justify-content:center;align-items:center;gap:8px}
.social{display:flex;gap:5px}
.social span{width:11px;height:11px;border-radius:50%;background:#bdbdbd}
</style>
</head>
<body>
<div class="page">
  <header class="site-header">
    <div class="brand"><span class="brand-dot"></span>medora</div>
    <nav class="main-nav">
      <a href="#">Health Packages</a>
      <a href="#">Appointments</a>
      <a href="#">Specialists</a>
    </nav>
  </header>

  <section class="hero">
    <svg class="hero-arrows" width="769" height="276" viewBox="0 0 769 276" aria-hidden="true">
      <path d="M196 180 Q220 165 240 180" fill="none" stroke="#777" stroke-width="1.5" stroke-dasharray="4 3"/>
      <path d="M236 175 l6 6 -8 2" fill="none" stroke="#777" stroke-width="1.5"/>
      <path d="M362 180 Q386 165 406 180" fill="none" stroke="#777" stroke-width="1.5" stroke-dasharray="4 3"/>
      <path d="M402 175 l6 6 -8 2" fill="none" stroke="#777" stroke-width="1.5"/>
    </svg>
    <div class="step" style="left:77px;top:74px">
      <div class="step-label">Select<b>A Package</b></div>
      <div class="step-circle"><div class="step-art" role="img" aria-label="Sketched wallet and package icon"></div></div>
    </div>
    <div class="step" style="left:243px;top:74px">
      <div class="step-label">Schedule an<b>Appointment at your convenience</b></div>
      <div class="step-circle"><div class="step-art" role="img" aria-label="Sketched calendar icon"></div></div>
    </div>
    <div class="step" style="left:410px;top:74px">
      <div class="step-label">Get your<b>Result Back</b></div>
      <div class="step-circle"><div class="step-art" role="img" aria-label="Sketched report sheet icon"></div></div>
    </div>
    <div class="tag-available">Available Now</div>
    <div class="doodle" role="img" aria-label="Hand-sketched cartoon doctor character"></div>
  </section>

  <section class="intro">
    <h1>Medora Healthcare Industry</h1>
    <p>Our care teams connect you with trusted doctors from home. Book visits in minutes, follow every result online and speak with a specialist who fits your needs. We keep your records safe, your time respected and your health plan clear, so you stay in charge of every step.</p>
  </section>

  <section class="cards">
    <article class="card">
      <div class="card-media a" role="img" aria-label="Medical technology illustration"></div>
      <h3>Litera Torquent</h3>
      <p>Short guidance from our team on care, tests and daily wellbeing.</p>
    </article>
    <article class="card">
      <div class="card-media b" role="img" aria-label="Clinical consultation illustration"></div>
      <h3>Litera Torquent</h3>
      <p>Simple advice from our doctors on checks, plans and healthy habits.</p>
    </article>
    <article class="card">
      <div class="card-media c" role="img" aria-label="Laboratory work illustration"></div>
      <h3>Litera Torquent</h3>
      <p>Clear notes from our lab on samples, results and what follows.</p>
    </article>
  </section>

  <section class="columns">
    <div class="col">
      <h2>Specialists</h2>
      <div class="specialist-media" role="img" aria-label="Glowing digital medicine illustration"></div>
      <p>Meet certified doctors across many fields and choose the one who suits your needs and schedule.</p>
      <a class="read-more" href="#">Read more</a>
    </div>
    <div class="col">
      <h2>Health Packages</h2>
      <p>Pick a plan that covers regular checks, lab tests and follow up visits with clear pricing.</p>
      <ul class="checks">
        <li><svg width="9" height="9" viewBox="0 0 10 10" aria-hidden="true"><path d="M1 5 L4 8 L9 2" fill="none" stroke="#7cbd3a" stroke-width="2"/></svg>Patient Care</li>
        <li><svg width="9" height="9" viewBox="0 0 10 10" aria-hidden="true"><path d="M1 5 L4 8 L9 2" fill="none" stroke="#7cbd3a" stroke-width="2"/></svg>Supportive Oncology</li>
        <li><svg width="9" height="9" viewBox="0 0 10 10" aria-hidden="true"><path d="M1 5 L4 8 L9 2" fill="none" stroke="#7cbd3a" stroke-width="2"/></svg>Integrative Health</li>
        <li><svg width="9" height="9" viewBox="0 0 10 10" aria-hidden="true"><path d="M1 5 L4 8 L9 2" fill="none" stroke="#7cbd3a" stroke-width="2"/></svg>Cancer Survivorship Lecture Series</li>
        <li><svg width="9" height="9" viewBox="0 0 10 10" aria-hidden="true"><path d="M1 5 L4 8 L9 2" fill="none" stroke="#7cbd3a" stroke-width="2"/></svg>Radiology Tests &amp; Procedures</li>
      </ul>
    </div>
    <div class="col">
      <h2>What Our Patients Say</h2>
      <div class="testimonial">
        <div class="avatar" role="img" aria-label="Patient portrait"></div>
        <p><b>Anna Morel</b>The booking was quick and my results arrived the next day. Highly recommended to all.</p>
      </div>
      <div class="testimonial">
        <div class="avatar" role="img" aria-label="Patient portrait"></div>
        <p><b>Lena Hart</b>I spoke with a specialist from my office in ten minutes. Clear advice and kind staff.</p>
      </div>
    </div>
  </section>

  <footer class="site-footer">
    <nav class="footer-nav">
      <a href="#">HOME</a><a href="#">ABOUT</a><a href="#">SERVICES</a><a href="#">PATIENT GUIDE</a><a href="#">NEUROLOGIST</a><a href="#">FAQ</a><a href="#">CONTACT</a>
    </nav>
    <div class="copyright">© 2015 - All Rights Reserved <span class="social"><span></span><span></span><span></span><span></span></span></div>
  </footer>
</div>
</body>
</html>
```